ORLA - Óptica Médica - web design and concept

Website concept - Create and develop our website design and structure. ORLA is an optical store chain, and we are looking to establish our web and digital concept. In attachment there are several pictures about our stores and our logo.

The website structure should be user friendly. Colors should be light and the design as simple and minimalist as possible. There are different variations of the logothat can be used, check the file.

The website will include optical collections and sun collections as an online store. Also, a medical menu should be considered in order for clients to schedule optometry appointments. There should also be a menu for client assistance where the clients can read about glass maintenance in our workshop.
Updates

Low design quality

Number of Pages Required

5+ page

Font styles to use
Serif
Sans Serif

Requirements
Must have
• Must be user-friendly and minimalist.
• Please USE PICTURES FROM THE BRANDS we sell: MERUN, BOSKA, PNW, KOLE, BAMPE
Nice to have
• Nice to inspire: ZEK glasses (see website https://ch.shopzek.com/en/)
• Nice to inspire: https://merun-eyewear.com/
• Nice to ispire: https://www.pnwglobe.com/en/
Should not have
• Hysteric colors and shapes

```html
<!DOCTYPE html>
<html lang="en">
<head>
<meta charset="utf-8">
<title>ORLA Vision Care — Contact us</title>
<link href="https://fonts.googleapis.com/css2?family=Raleway:wght@400;500;600&family=Lato:wght@400;700&display=swap" rel="stylesheet">
<style>
:root{
  --ink:#1a1a1a;
  --muted:#6a6a6a;
  --panel:#f6f6f6;
  --field-line:#e8e8e8;
  --bubble:#f3f3f3;
  --footer:#232323;
  --footer-text:#ffffff;
  --footer-line:#5a5a5a;
}
*{margin:0;padding:0;box-sizing:border-box}
html,body{width:824px;height:1200px;overflow:hidden;background:#fff}
body{position:relative;font-family:"Lato",sans-serif;color:var(--ink)}
.abs{position:absolute}

.header-phone{left:84px;top:52px;display:flex;align-items:center;gap:7px;font-size:10.5px}
.brand{left:0;width:824px;top:56px;text-align:center;font-family:"Raleway",sans-serif;font-weight:500;font-size:21px;letter-spacing:4px}
.header-icons{left:655px;top:54px;display:flex;gap:12px;align-items:center}

.page-title{left:0;width:824px;top:145px;text-align:center;font-family:"Raleway",sans-serif;font-size:29px;font-weight:400}

.feedback{left:81px;top:214px;width:665px;height:358px;background:var(--panel)}
.feedback-title{position:absolute;left:0;width:665px;top:20px;text-align:center;font-family:"Raleway",sans-serif;font-size:25px;font-weight:500}
.feedback-rule{position:absolute;left:169px;top:62px;width:274px;height:1px;background:#d4d4d4}
.field-label{position:absolute;font-size:10.5px;letter-spacing:1px;color:var(--muted)}
.field{position:absolute;height:27px;width:271px;border:1px solid var(--field-line);background:var(--panel)}
.field.message{height:70px;width:559px}
.send-btn{position:absolute;left:23px;top:310px;width:271px;height:28px;background:#000;color:#fff;font-size:10.5px;font-weight:700;letter-spacing:1.6px;display:flex;align-items:center;justify-content:center}

.bubble{width:68px;height:68px;border-radius:50%;background:var(--bubble);display:flex;align-items:center;justify-content:center;top:646px}
.info-text{font-size:10.5px;letter-spacing:1px;color:var(--muted);line-height:12.5px}
.hours{display:grid;grid-template-columns:46px auto}

.footer{left:0;top:904px;width:824px;height:296px;background:var(--footer);color:var(--footer-text)}
.footer-brand{position:absolute;left:82px;top:52px;width:80px;text-align:center;font-family:"Raleway",sans-serif;font-size:16px;letter-spacing:3px}
.rule{position:absolute;height:2px;background:#fff}
.footer-about{position:absolute;left:82px;top:102px;font-size:10px;line-height:12px}
.footer-contact{position:absolute;left:82px;top:132px;font-size:10px;line-height:15px}
.footer-contact div{display:flex;align-items:center;gap:6px}
.pay{position:absolute;top:187px;display:flex;gap:6px;left:83px}
.pay span{width:29px;height:17px;background:#fff;color:#232323;font-size:7px;font-weight:700;display:flex;align-items:center;justify-content:center}
.col-head{position:absolute;top:60px;font-family:"Raleway",sans-serif;font-size:10.5px;font-weight:500;letter-spacing:.2px}
.links{position:absolute;left:283px;top:102px;list-style:none;font-size:9.5px;line-height:14.4px}
.links li{display:flex;align-items:center;gap:8px}
.links li::before{content:"";width:6px;height:6px;border-radius:50%;background:#fff}
.tags{position:absolute;left:412px;top:99px;display:grid;grid-template-columns:repeat(3,41px);column-gap:9px;row-gap:9px}
.tags span{height:17px;border:1px solid #fff;font-size:9.5px;display:flex;align-items:center;justify-content:center}
.tags span.dark{background:#000;border-color:#000}
.gallery{position:absolute;left:583px;top:99px;display:grid;grid-template-columns:repeat(3,51px);gap:4px 4px}
.gallery div{height:47px}
.bottom-line{position:absolute;left:0;top:265px;width:824px;height:1px;background:var(--footer-line)}
.copyright{position:absolute;left:82px;top:274px;font-size:10.5px}
.social{position:absolute;left:619px;top:271px;display:flex;gap:9px}
.social span{width:18px;height:18px;border-radius:50%;background:#fff}
</style>
</head>
<body>

<div class="abs header-phone">
  <svg width="14" height="14" viewBox="0 0 14 14" fill="none" stroke="#1a1a1a" stroke-width="1"><circle cx="7" cy="7" r="6.3"/><path d="M5 4.2l1 1.6-.7.8c.5 1 1.2 1.7 2.2 2.2l.8-.7 1.6 1-.6 1.1c-2.6-.4-4.6-2.4-5-5z"/></svg>
  <span>123-456-7890</span>
</div>
<div class="abs brand">ORLA</div>
<div class="abs header-icons">
  <svg width="10" height="10" viewBox="0 0 10 10" fill="none" stroke="#1a1a1a"><path d="M5 8.8L1.3 5A2.2 2.2 0 015 2.2 2.2 2.2 0 018.7 5z"/></svg>
  <svg width="12" height="10" viewBox="0 0 12 10" fill="none" stroke="#1a1a1a"><path d="M.5 1h2l1.4 5h6l1.2-3.7H3"/><circle cx="4.5" cy="8.5" r=".8"/><circle cx="9" cy="8.5" r=".8"/></svg>
  <svg width="11" height="11" viewBox="0 0 11 11" fill="none" stroke="#1a1a1a"><circle cx="4.5" cy="4.5" r="3.3"/><path d="M7 7l3.4 3.4" stroke-width="1.6"/></svg>
  <svg width="12" height="10" viewBox="0 0 12 10" fill="#1a1a1a" style="margin-left:8px"><rect y="0" width="12" height="2"/><rect y="4" width="12" height="2"/><rect y="8" width="12" height="2"/></svg>
</div>

<h1 class="abs page-title">Contact us</h1>

<section class="abs feedback">
  <h2 class="feedback-title">Send us Your Feedback</h2>
  <div class="feedback-rule"></div>
  <span class="field-label" style="left:22px;top:78px">Name</span>
  <span class="field-label" style="left:310px;top:79px">Phone</span>
  <div class="field" style="left:23px;top:99px"></div>
  <div class="field" style="left:311px;top:99px"></div>
  <span class="field-label" style="left:22px;top:141px">E-Mail</span>
  <span class="field-label" style="left:310px;top:139px">Subject</span>
  <div class="field" style="left:23px;top:158px"></div>
  <div class="field" style="left:311px;top:158px"></div>
  <span class="field-label" style="left:22px;top:201px">Message</span>
  <div class="field message" style="left:23px;top:218px"></div>
  <div class="send-btn">SEND MESSAGE</div>
</section>

<div class="abs bubble" style="left:117px">
  <svg width="30" height="30" viewBox="0 0 30 30" fill="none" stroke="#1a1a1a" stroke-width="1.4"><path d="M6 3l5 6-2.5 3c1.8 3.8 4.6 6.6 8.5 8.5l3-2.5 6 5-3 4C12 26 4 18 2.5 7z"/></svg>
</div>
<div class="abs bubble" style="left:375px">
  <svg width="32" height="32" viewBox="0 0 32 32" fill="none" stroke="#1a1a1a" stroke-width="1.8"><circle cx="16" cy="16" r="14"/><path d="M16 7v9l5 5"/></svg>
</div>
<div class="abs bubble" style="left:642px">
  <svg width="34" height="24" viewBox="0 0 34 24" fill="none" stroke="#1a1a1a" stroke-width="1.4"><rect x="1" y="1" width="32" height="22"/><path d="M1 1l16 13L33 1M1 23l12-11M33 23L21 12"/></svg>
</div>

<div class="abs info-text" style="left:108px;top:740px">+012-345-678-9<br>+012-345-678-9</div>
<div class="abs info-text hours" style="left:340px;top:734px">
  <span>Mon</span><span>: 2:30pm - 7:00pm</span>
  <span>Tue-Thr</span><span>: 9:30am -1:30pm</span>
  <span>Sat</span><span>: 2:30pm -7:00pm</span>
  <span style="grid-column:1/3">(Sunday Closed</span>
</div>
<div class="abs info-text" style="left:612px;top:733px">Info@orlavisioncare.com</div>

<footer class="abs footer">
  <div class="footer-brand">ORLA</div>
  <div class="rule" style="left:82px;top:87px;width:80px"></div>
  <p class="footer-about">Lorem Ipsum is simply dummy text<br>ipsum is simply the &nbsp;dummy... &#x2794;</p>
  <div class="footer-contact">
    <div><svg width="9" height="8" viewBox="0 0 9 8" fill="#fff"><path d="M0 3c1-2 8-2 9 0L7 4 6 3H3L2 4zM2 5h5l1 3H1z"/></svg>Phone: 123 456 7890</div>
    <div><svg width="9" height="7" viewBox="0 0 9 7" fill="none" stroke="#fff"><rect x=".5" y=".5" width="8" height="6"/><path d="M.5.5l4 3 4-3"/></svg>Email:info@orla.com</div>
    <div><svg width="9" height="10" viewBox="0 0 9 10" fill="#fff"><path d="M4.5 0a3.5 3.5 0 013.5 3.5C8 6 4.5 10 4.5 10S1 6 1 3.5A3.5 3.5 0 014.5 0z"/><circle cx="4.5" cy="3.5" r="1.2" fill="#232323"/></svg>Address : 12th Street, City .Usa</div>
  </div>
  <div class="pay"><span>Paylo</span><span>Marketa</span><span>Skora</span><span>Vexa</span><span>Disca</span></div>

  <h3 class="col-head" style="left:283px">INFORMATION</h3>
  <div class="rule" style="left:283px;top:82px;width:56px"></div>
  <ul class="links">
    <li>Home</li><li>Woman</li><li>Men</li><li>Kids</li><li>Testimonials</li><li>Blogs</li><li>Contact us</li>
  </ul>

  <h3 class="col-head" style="left:412px">POPULAR TAGE</h3>
  <div class="rule" style="left:412px;top:82px;width:47px"></div>
  <div class="tags">
    <span>Kids</span><span>Men</span><span>Lady</span>
    <span>Woman</span><span>Latest</span><span>Specials</span>
    <span>Faishion</span><span>Eye</span><span>offers</span>
    <span class="dark">Faishion</span><span>COOL</span>
  </div>

  <h3 class="col-head" style="left:581px">PICSTREAM</h3>
  <div class="rule" style="left:581px;top:82px;width:34px"></div>
  <div class="gallery">
    <div role="img" aria-label="Portrait of a woman wearing glasses" style="background:linear-gradient(#c9b4a4,#7e5a45)"></div>
    <div role="img" aria-label="Woman in teal sunglasses" style="background:linear-gradient(#cfd3d4,#9aa3a6)"></div>
    <div role="img" aria-label="Woman with red hair adjusting glasses" style="background:linear-gradient(#e0d4cf,#a0503d)"></div>
    <div role="img" aria-label="Woman holding glasses" style="background:linear-gradient(#e2dcd5,#b59a84)"></div>
    <div role="img" aria-label="Man with beard wearing glasses" style="background:linear-gradient(#d8d8d8,#6e5649)"></div>
    <div role="img" aria-label="Man smiling in glasses" style="background:linear-gradient(#eeeeee,#c49c84)"></div>
  </div>

  <div class="bottom-line"></div>
  <p class="copyright">CopyRight &copy;2018 ORLA Vision Care. All Right Reserve</p>
  <div class="social" aria-label="Social links"><span></span><span></span><span></span><span></span><span></span></div>
</footer>

</body>
</html>
```